New Business Card for Web Design/Internet Marketing Company

Looking for a great looking new business card. We are a 10 year old web design, internet marketing and website management company that works mostly with small businesses.

Our new card needs to better match the colors and style of our website, be bold, extremely usable and slightly edgy.

Target Market(s)

Small/Medium businesses that have websites

Industry/Entity Type

Internet

Requirements
Must have
• Front and back design, full color, rounded corners please

Must use the colors/style of our website (JPG provided)

INFO FOR CARDS (as readable as possible please)
Mark Lenner
President/CEO
mark@trelvanmedia.example
Phone: 520-381-7459
Toll Free: 866-381-7459
Address: 4315 W. Calloway Ave. Ste. 140, Tucson, AZ 85792

THINGS I WANT TO PROMOTE (if there is room):
1. Our Website - www.trelvanmedia.example

2. Social Media
Twitter: @trelvanmedia
Facebook: www.facebook.com/trelvanmedia

3. Our Services
Web Design
Internet Marketing
Website Management

```html
<!DOCTYPE html>
<html lang="en">
<head>
<meta charset="utf-8">
<title>Trelvan Media – Business Card</title>
<link rel="stylesheet" href="https://fonts.googleapis.com/css2?family=Open+Sans:wght@400;600;700&display=swap">
<style>
  :root {
    --brand-blue: #1b92cd;
    --brand-orange: #f0862a;
    --ink: #4a4a4a;
    --rule: #9a9a9a;
    --paper: #ffffff;
    --backdrop: #ececec;
  }
  * { box-sizing: border-box; margin: 0; padding: 0; }
  html, body {
    width: 1200px; height: 1078px; overflow: hidden;
    background: var(--backdrop);
    font-family: "Open Sans", Arial, sans-serif;
  }
  .canvas { position: relative; width: 1200px; height: 1078px; }

  .card {
    position: absolute;
    width: 760px; height: 435px;
    border-radius: 29px;
    overflow: hidden;
  }

  /* Front */
  .card-front { left: 77px; top: 73px; background: var(--paper); }
  .card-front .wave { position: absolute; inset: 0; }
  .brand {
    position: absolute; left: 52px; top: 190px;
    display: flex; align-items: center; gap: 12px;
  }
  .brand-dot {
    width: 22px; height: 22px; border-radius: 50%;
    background: var(--brand-blue);
  }
  .brand-name {
    font-size: 44px; font-weight: 600; color: var(--brand-orange);
    letter-spacing: -0.5px; line-height: 1;
  }
  .tagline {
    position: absolute; left: 150px; top: 252px;
    font-size: 17px; color: var(--ink);
  }
  .divider {
    position: absolute; left: 424px; top: 87px;
    width: 2px; height: 199px; background: var(--rule); opacity: .6;
  }
  .contact-list {
    position: absolute; left: 457px; top: 100px;
    list-style: none; font-size: 19px; color: var(--ink);
  }
  .contact-list li {
    display: flex; align-items: center; gap: 9px;
    height: 27.5px;
  }
  .contact-list svg { width: 14px; height: 14px; fill: var(--ink); flex: none; }
  .address {
    position: absolute; left: 457px; top: 230px;
    font-size: 19px; line-height: 28px; color: var(--ink);
  }
  .signature {
    position: absolute; left: 0; right: 0; top: 393px;
    text-align: center; color: var(--paper);
  }
  .signature .person { font-size: 23px; font-weight: 700; }
  .signature .role { font-size: 19px; }

  /* Back */
  .card-back {
    left: 380px; top: 569px;
    background: var(--brand-blue);
    color: var(--paper); text-align: center;
  }
  .services-title {
    position: absolute; left: 0; right: 0; top: 145px;
    font-size: 31px; font-weight: 700;
  }
  .services-list {
    position: absolute; left: 0; right: 0; top: 204px;
    list-style: none; font-size: 28px; font-weight: 700; line-height: 39px;
  }
  .services-list li { display: inline-block; margin: 0 8px; }
  .services-list li::before { content: "\2022\00a0"; }
  .services-list .break { display: block; }
  .social {
    position: absolute; left: 0; right: 0; top: 362px;
    display: flex; justify-content: center; gap: 26px;
    font-size: 26px;
  }
  .social span { display: flex; align-items: center; gap: 9px; }
  .social i {
    display: inline-block; width: 20px; height: 20px;
    background: #e3f2fa; border-radius: 3px;
  }
</style>
</head>
<body>
<main class="canvas">

  <section class="card card-front" aria-label="Business card front">
    <svg class="wave" viewBox="0 0 760 435" preserveAspectRatio="none" aria-hidden="true">
      <path d="M0 286 Q 330 366 640 386 Q 330 376 0 300 Z" fill="var(--brand-orange)"/>
      <path d="M0 314 Q 380 398 760 344 L760 435 L0 435 Z" fill="var(--brand-blue)"/>
    </svg>

    <div class="brand">
      <span class="brand-dot"></span>
      <span class="brand-name">trelvan media</span>
    </div>
    <p class="tagline">Built for small business</p>

    <div class="divider"></div>

    <ul class="contact-list">
      <li><svg viewBox="0 0 24 24"><path d="M6.6 10.8a15 15 0 0 0 6.6 6.6l2.2-2.2c.3-.3.7-.4 1-.2 1.1.4 2.3.6 3.6.6.6 0 1 .4 1 1V20c0 .6-.4 1-1 1A17 17 0 0 1 3 4c0-.6.4-1 1-1h3.5c.6 0 1 .4 1 1 0 1.3.2 2.5.6 3.6.1.3 0 .7-.2 1z"/></svg>866-381-7459</li>
      <li><svg viewBox="0 0 24 24"><path d="M6.6 10.8a15 15 0 0 0 6.6 6.6l2.2-2.2c.3-.3.7-.4 1-.2 1.1.4 2.3.6 3.6.6.6 0 1 .4 1 1V20c0 .6-.4 1-1 1A17 17 0 0 1 3 4c0-.6.4-1 1-1h3.5c.6 0 1 .4 1 1 0 1.3.2 2.5.6 3.6.1.3 0 .7-.2 1z"/></svg>520-381-7459</li>
      <li><svg viewBox="0 0 24 24"><path d="M2 5h20v14H2z M4 7v1l8 5 8-5V7l-8 5z" fill-rule="evenodd"/></svg>mark@trelvanmedia.example</li>
      <li><svg viewBox="0 0 24 24"><path d="M12 2a10 10 0 1 0 0 20 10 10 0 0 0 0-20zm-8 9h16v2H4zm0-4h16v1.6H4zm0 8.4h16V17H4z"/></svg>www.trelvanmedia.example</li>
    </ul>

    <p class="address">4315 W. Calloway Ave. Ste. 140<br>Tucson, AZ 85792</p>

    <p class="signature"><span class="person">Mark Lenner ,</span> <span class="role">President/CEO</span></p>
  </section>

  <section class="card card-back" aria-label="Business card back">
    <h2 class="services-title">Our Services</h2>
    <ul class="services-list">
      <li>Web Design</li><li>Internet Marketing</li>
      <li class="break">Website Management</li>
    </ul>
    <p class="social">
      <span><i></i>@trelvanmedia</span>
      <span><i></i>trelvanmedia</span>
    </p>
  </section>

</main>
</body>
</html>
```